Brimlow Plumbing Solutions

This is for my new plumbing company, I have attached an example of what I’m going for but want it to look better.

Target Market(s)

Home owners, real estate, etc.

Industry/Entity Type

Plumbing

Font styles to use
Other font styles liked:
• As per my logo and other examples uploaded

Colors

Designer to choose colors to be used in the design.

Requirements
Must have
• Must include my logo provided and similar to my flyer I have attached but better

```html
<!DOCTYPE html>
<html lang="en">
<head>
<meta charset="utf-8">
<title>Brimlow Plumbing Solutions – Flyer</title>
<link href="https://fonts.googleapis.com/css2?family=Inter:wght@400;500;600;700;800&display=swap" rel="stylesheet">
<style>
  :root {
    --navy: #1b2f66;
    --blue: #3a9ad9;
    --blue-mid: #5aaee3;
    --blue-light: #a9cdec;
    --blue-pale: #cfe3f5;
    --ink: #1d2333;
    --white: #ffffff;
  }
  * { margin: 0; padding: 0; box-sizing: border-box; }
  html, body { width: 1200px; height: 1200px; overflow: hidden; background: var(--white); }
  body { font-family: "Inter", Arial, sans-serif; color: var(--ink); }

  .flyer { position: relative; width: 1200px; height: 1200px; overflow: hidden; background: var(--white); }
  .decor { position: absolute; inset: 0; }

  .mascot-area {
    position: absolute; left: 760px; top: 70px; width: 400px; height: 380px;
    border-radius: 50%;
    background: radial-gradient(ellipse at 50% 50%, var(--navy) 0%, var(--navy) 45%, rgba(27,47,102,0.55) 62%, rgba(58,154,217,0) 72%);
  }

  .brand { position: absolute; left: 65px; top: 110px; display: flex; align-items: center; gap: 16px; }
  .brand-dot { width: 26px; height: 26px; border-radius: 50%; background: var(--navy); flex: none; }
  .brand-name { font-size: 36px; font-weight: 700; color: var(--navy); line-height: 1.15; width: 330px; }
  .tagline { position: absolute; left: 65px; top: 228px; font-size: 25px; font-weight: 600; color: var(--navy); }

  .values { position: absolute; left: 68px; top: 372px; font-size: 20px; }
  .intro-title { position: absolute; left: 65px; top: 430px; font-size: 37px; font-weight: 700; color: var(--navy); }
  .intro-text { position: absolute; left: 65px; top: 500px; width: 470px; font-size: 27px; line-height: 1.32; }
  .tone { position: absolute; left: 68px; top: 630px; font-size: 22px; }

  .offer {
    position: absolute; left: 562px; top: 488px; width: 680px; height: 156px;
    background: var(--blue); border-radius: 78px 0 0 78px;
    color: var(--white); font-size: 29px; font-weight: 600; line-height: 1.25;
    padding: 44px 0 0 52px;
  }
  .offer-badge {
    position: absolute; left: 1050px; top: 410px; width: 116px; height: 116px; border-radius: 50%;
    background: var(--white); box-shadow: 0 3px 8px rgba(0,0,0,0.12);
    display: flex; align-items: center; justify-content: center;
    font-size: 16px; font-weight: 700; color: var(--blue); transform: rotate(-12deg);
  }

  .services-title { position: absolute; left: 304px; top: 718px; font-size: 40px; font-weight: 700; color: var(--navy); }
  .service-list { position: absolute; list-style: none; }
  .service-list li { display: flex; align-items: center; gap: 22px; font-size: 26px; height: 37px; white-space: nowrap; }
  .service-list.left { left: 303px; top: 800px; }
  .service-list.left li { height: 41px; }
  .service-list.right { left: 761px; top: 798px; }
  .service-list.right li { gap: 20px; }
  .svc-icon { width: 34px; height: 34px; flex: none; }
  .svc-blank { width: 34px; flex: none; }

  .contact-bar {
    position: absolute; left: 0; top: 1064px; width: 1200px; height: 136px;
    background: var(--navy); color: var(--white);
  }
  .contact { position: absolute; display: flex; align-items: center; gap: 22px; font-size: 28px; font-weight: 500; line-height: 1.3; }
  .contact.phone { left: 52px; top: 28px; }
  .contact.email { left: 500px; top: 28px; }
  .contact-icon { width: 48px; height: 48px; flex: none; }
  .divider { position: absolute; left: 430px; top: 36px; width: 2px; height: 66px; background: rgba(255,255,255,0.55); }
</style>
</head>
<body>
<main class="flyer">
  <svg class="decor" width="1200" height="1200" viewBox="0 0 1200 1200" aria-hidden="true">
    <polygon points="560,0 1200,0 1200,560 1000,560 640,150" fill="var(--blue)"/>
    <polygon points="640,250 660,232 1200,640 1200,662" fill="var(--blue-light)"/>
    <polygon points="810,415 826,400 1030,660 1012,672" fill="var(--blue-light)"/>
    <polygon points="560,340 578,325 740,560 722,572" fill="var(--blue-pale)"/>
    <polygon points="0,900 0,1064 150,1064" fill="var(--blue-pale)"/>
    <polygon points="0,780 0,810 330,1100 350,1085" fill="var(--blue-light)"/>
    <polygon points="60,920 80,900 340,1060 320,1080" fill="var(--blue-mid)"/>
    <polygon points="0,700 0,720 200,880 215,868" fill="var(--blue-pale)"/>
  </svg>

  <div class="mascot-area" role="img" aria-label="Large brand mascot silhouette in navy"></div>

  <div class="brand"><span class="brand-dot"></span><span class="brand-name">Brimlow Plumbing Solutions</span></div>
  <p class="tagline">Reliable Plumbing. Real Solutions.</p>

  <p class="values">Confidence, reliability and expert craftsmanship</p>
  <h2 class="intro-title">Intro &amp; Highlights</h2>
  <p class="intro-text">Your local reliable Sydney plumber — specialising in Plumbing, Drainage &amp; Gas Maintenance.</p>
  <p class="tone">Friendly, authoritative service you can trust.</p>

  <div class="offer">Mention this flyer to receive<br>15% OFF your first service.</div>
  <div class="offer-badge">KEY OFFER</div>

  <h2 class="services-title">Our Services</h2>
  <ul class="service-list left">
    <li><svg class="svc-icon" viewBox="0 0 34 34"><circle cx="17" cy="17" r="15" fill="none" stroke="var(--blue)" stroke-width="2.5"/><path d="M11 20l6-8 6 8z" fill="var(--blue)"/></svg>Emergency plumbing</li>
    <li><svg class="svc-icon" viewBox="0 0 34 34"><circle cx="17" cy="17" r="15" fill="none" stroke="var(--blue)" stroke-width="2.5"/><rect x="10" y="14" width="14" height="6" rx="2" fill="var(--blue)"/></svg>Plumbing maintenance</li>
    <li><svg class="svc-icon" viewBox="0 0 34 34"><circle cx="17" cy="17" r="15" fill="none" stroke="var(--blue)" stroke-width="2.5"/><path d="M10 12h14l-4 10h-6z" fill="var(--blue)"/></svg>Drainage maintenance</li>
    <li><svg class="svc-icon" viewBox="0 0 34 34"><circle cx="17" cy="17" r="15" fill="none" stroke="var(--blue)" stroke-width="2.5"/><rect x="10" y="10" width="14" height="14" fill="none" stroke="var(--blue)" stroke-width="2"/><path d="M12 12l10 10M22 12l-10 10" stroke="var(--blue)" stroke-width="2"/></svg>Leaking fixtures</li>
  </ul>
  <ul class="service-list right">
    <li><svg class="svc-icon" viewBox="0 0 34 34"><path d="M6 8h12v4H6z" fill="var(--blue)"/><path d="M18 10h6v6" fill="none" stroke="var(--blue)" stroke-width="3"/><path d="M21 20c-3 4-3 7 0 8 3-1 3-4 0-8z" fill="var(--blue)"/></svg>Hot water systems</li>
    <li><span class="svc-blank"></span>Gas</li>
    <li><svg class="svc-icon" viewBox="0 0 34 34"><circle cx="17" cy="17" r="15" fill="none" stroke="var(--blue)" stroke-width="2.5"/><path d="M17 9v16M12 14l5 5 5-5" fill="none" stroke="var(--blue)" stroke-width="2"/></svg>Leaking systems</li>
    <li><svg class="svc-icon" viewBox="0 0 34 34"><circle cx="17" cy="17" r="15" fill="none" stroke="var(--blue)" stroke-width="2.5"/><rect x="12" y="10" width="10" height="14" rx="1" fill="none" stroke="var(--blue)" stroke-width="2"/></svg>Blocked sewer &amp; stormwater</li>
    <li><svg class="svc-icon" viewBox="0 0 34 34"><circle cx="17" cy="17" r="15" fill="none" stroke="var(--blue)" stroke-width="2.5"/><circle cx="17" cy="17" r="5" fill="var(--blue)"/></svg>Camera &amp; locating</li>
    <li><svg class="svc-icon" viewBox="0 0 34 34"><circle cx="17" cy="17" r="15" fill="none" stroke="var(--blue)" stroke-width="2.5"/><path d="M12 24V14M17 24V10M22 24V14" stroke="var(--blue)" stroke-width="2"/></svg>TMV maintenance</li>
  </ul>

  <footer class="contact-bar">
    <div class="contact phone">
      <svg class="contact-icon" viewBox="0 0 48 48"><path d="M14 6l7 8-4 5c2 5 6 9 11 11l5-4 8 7-4 7C23 40 8 25 7 11z" fill="none" stroke="var(--white)" stroke-width="2.5" stroke-linejoin="round"/></svg>
      <span>0491 570 156<br>#00A9E1</span>
    </div>
    <span class="divider"></span>
    <div class="contact email">
      <svg class="contact-icon" viewBox="0 0 48 48"><circle cx="22" cy="22" r="18" fill="none" stroke="var(--white)" stroke-width="2.5"/><circle cx="22" cy="22" r="7" fill="none" stroke="var(--white)" stroke-width="2.5"/><rect x="28" y="32" width="14" height="11" rx="2" fill="var(--navy)" stroke="var(--white)" stroke-width="2.5"/></svg>
      <span>brimlowplumbing@mailbox.com<br>@mailbox.com</span>
    </div>
  </footer>
</main>
</body>
</html>
```